Keystone Trench Co Business Card*

Looking for a professional, clean and crisp business card

I am in the underground utilities industry and am just looking for a really impressive business card. I would like our card to be white with our symbol crisp and clear with it protruding. I also have a business partner that will require his name and info on the card once the design is set. I would like to have our website info on the card which is;
http://keystonetrenchco.example/

Contact Information for Business Card

Website, contact name, number and email

```html
<!DOCTYPE html>
<html lang="en">
<head>
<meta charset="utf-8">
<title>Keystone Trench Co Business Card</title>
<link rel="stylesheet" href="https://fonts.googleapis.com/css2?family=Lato:wght@400;700&display=swap">
<style>
  :root {
    --page-bg: #e9e7e3;
    --card-white: #ffffff;
    --card-dark: #1d1e21;
    --card-dark-edge: #2c2d31;
    --accent-blue: #3c7dc2;
    --ink-grey: #4a4b4f;
    --ink-white: #f4f4f4;
  }
  * { box-sizing: border-box; margin: 0; padding: 0; }
  html, body {
    width: 1200px; height: 1200px; overflow: hidden;
    background: var(--page-bg);
    font-family: "Lato", sans-serif;
  }
  .sheet {
    width: 1200px; height: 1200px;
    display: flex; flex-direction: column;
    align-items: center; justify-content: center; gap: 70px;
  }
  .card {
    position: relative;
    width: 860px; height: 491px;
    border-radius: 4px;
    box-shadow: 0 10px 28px rgba(0,0,0,0.18);
    overflow: hidden;
  }
  /* Back side: contact details */
  .card-back {
    background: linear-gradient(115deg, var(--card-dark) 0%, var(--card-dark) 45%, var(--card-dark-edge) 70%, var(--card-dark) 100%);
    color: var(--ink-white);
  }
  .contact {
    position: absolute; left: 70px; top: 150px;
  }
  .contact-name {
    color: var(--accent-blue);
    font-weight: 700; font-size: 34px;
    margin-bottom: 18px;
  }
  .contact-line {
    display: flex; align-items: center; gap: 18px;
    font-size: 27px; line-height: 1.5;
  }
  .contact-line svg { width: 24px; height: 24px; flex: none; }
  .brand-mark {
    position: absolute; right: 60px; top: 50%;
    transform: translateY(-50%);
    display: flex; flex-direction: column; align-items: center; gap: 16px;
  }
  .brand-dot {
    width: 44px; height: 44px; border-radius: 50%;
    background: var(--accent-blue);
  }
  .brand-name {
    font-weight: 700; font-size: 30px; color: var(--ink-white);
    text-align: center; line-height: 1.2; max-width: 260px;
  }
  /* Front side: name and website */
  .card-front {
    background: var(--card-white);
  }
  .front-brand {
    position: absolute; left: 0; right: 0; top: 130px;
    display: flex; flex-direction: column; align-items: center; gap: 20px;
  }
  .front-brand .brand-dot { width: 60px; height: 60px; }
  .front-brand .brand-name {
    color: var(--ink-grey); font-size: 44px; max-width: none;
  }
  .front-url {
    position: absolute; left: 0; right: 0; bottom: 110px;
    text-align: center;
    color: var(--accent-blue); font-size: 30px;
  }
</style>
</head>
<body>
<main class="sheet">
  <section class="card card-back" aria-label="Business card back">
    <div class="contact">
      <p class="contact-name">Person Name</p>
      <p class="contact-line">
        <svg viewBox="0 0 24 24" fill="none" stroke="#3c7dc2" stroke-width="2"><rect x="6" y="2" width="12" height="20" rx="2"/><line x1="11" y1="18" x2="13" y2="18"/></svg>
        555-014-2288
      </p>
      <p class="contact-line">
        <svg viewBox="0 0 24 24" fill="none" stroke="#3c7dc2" stroke-width="2"><rect x="2" y="5" width="20" height="14" rx="1"/><polyline points="2,5 12,13 22,5"/></svg>
        info@keystonetrenchco.example
      </p>
      <p class="contact-line">
        <svg viewBox="0 0 24 24" fill="none" stroke="#3c7dc2" stroke-width="2"><circle cx="12" cy="12" r="10"/><ellipse cx="12" cy="12" rx="4" ry="10"/><line x1="2" y1="12" x2="22" y2="12"/></svg>
        www.keystonetrenchco.example
      </p>
    </div>
    <div class="brand-mark">
      <span class="brand-dot"></span>
      <span class="brand-name">Keystone Trench Co</span>
    </div>
  </section>

  <section class="card card-front" aria-label="Business card front">
    <div class="front-brand">
      <span class="brand-dot"></span>
      <span class="brand-name">Keystone Trench Co</span>
    </div>
    <p class="front-url">www.keystonetrenchco.example</p>
  </section>
</main>
</body>
</html>
```